Luxury Real Estate Website, Midwest, United States

We need web design services for a luxury website. We need IDX Integration with our MLS. We want this to be a very simple website with amazing graphics. We want it to link up with our MailChimp account in order to generate leads through a "More Information" Pop up on the main page. We want the main page to be covered with one large graphic that is a rolling slideshow of active listings of $400,000 and up from the IDX Integration. We need this website to give a very exclusive and sleek look. Lots of black is good... I will upload our logos in Black and Silver. We will also need an "About" page that we are going to call "Qeno Info". We want our graphics to be extremely impressive. Keep in mind, we are a company in the Midwest of the United States, and our real estate has a different look than homes in California or Florida. We need graphics that are realistic for the Midwest, yet still high-end.
Target Market(s)
Luxury Homeowners in the Midwest United States. The graphics needs to be pristine.
Industry/Entity Type
Real Estate
Coding
Coded - Design and coding required
Number of Pages Required
3 page
Requirements
Must have
- Large graphics with IDX Integration. The photos of real estate need to represent real estate that is common in the Midwest, United States. We also need MailChimp integration. We need a pop up that is titled "My Free Market Analysis" that makes them fill out a contact form asking for Full Name, Email Address, Phone Number and Address. This needs to be a pop up on the front page and will integrate with our MailChimp account. We also need a page called "About Qe No Home". And another page where clients can download informational PDFs. The main component needs to be a front page search engine connected with the IDX to access active listings from our MLS. I attached our logos and a sample front page of a website. I would love for ours to look similar.
Nice to have
- Lake House photos on midwest lakes are a plus.
Should not have
- Should not have clutter. This website needs to be clean, luxurious and exclusive.

```html
<!DOCTYPE html>
<html lang="en">
<head>
<meta charset="utf-8">
<title>Northfield Realty Group</title>
<link href="https://fonts.googleapis.com/css2?family=Roboto:wght@300;400;500;700&display=swap" rel="stylesheet">
<style>
:root{
  --black:#000;
  --ink:#0b0b0b;
  --footer:#121212;
  --bar:#1c1c1c;
  --white:#fff;
  --light:#f1f1f1;
  --grey:#8a8a8a;
  --muted:#bdbdbd;
  --text:#555;
  --line:#3a3a3a;
  --accent:#2a6fb0;
}
*{box-sizing:border-box;margin:0;padding:0}
html,body{width:1200px;height:3208px;overflow:hidden}
body{font-family:"Roboto",Arial,sans-serif;background:var(--black);color:var(--white);position:relative}
a{color:inherit;text-decoration:none}

/* header */
.site-header{position:absolute;top:0;left:0;width:1200px;height:96px;z-index:5;display:flex;align-items:center;justify-content:space-between;padding:0 60px 0 130px}
.brand{display:flex;align-items:center;gap:10px}
.brand-mark{width:14px;height:14px;background:var(--white)}
.brand-name{font-size:24px;font-weight:500;letter-spacing:3px;color:var(--white)}
.main-nav{display:flex;gap:30px;font-size:12px;font-weight:500;letter-spacing:.5px}

/* hero */
.hero{position:absolute;top:0;left:0;width:1200px;height:780px}
.hero-photo{position:absolute;inset:0;background:linear-gradient(180deg,#3c4f66 0%,#6d7f8f 22%,#3d5a3a 42%,#2f4a2c 55%,#5f7a6a 66%,#26332a 82%,#0c0f0c 100%)}
.hero-content{position:absolute;top:230px;left:0;width:1200px;text-align:center}
.hero-brand{display:inline-flex;align-items:center;gap:14px}
.hero-brand .brand-mark{width:22px;height:22px}
.hero-brand .brand-name{font-size:46px;letter-spacing:5px}
.hero-tagline{margin:26px auto 0;width:420px;font-size:17px;line-height:24px;color:var(--white)}
.search-bar{margin:34px auto 0;width:500px;height:44px;background:var(--white);display:flex;align-items:center;justify-content:space-between;padding:0 0 0 14px}
.search-bar span{color:#333;font-size:13px}
.search-btn{width:44px;height:44px;background:var(--accent);display:flex;align-items:center;justify-content:center}
.slide-arrow{position:absolute;top:336px;width:30px;height:30px;border-radius:50%;background:rgba(0,0,0,.55);display:flex;align-items:center;justify-content:center}
.slide-arrow.prev{left:98px}
.slide-arrow.next{right:98px}
.hero-curve{position:absolute;left:0;bottom:0;width:1200px;height:90px}

/* features */
.features{position:absolute;top:780px;left:0;width:1200px;height:380px;background:var(--black)}
.feature{position:absolute;top:40px;width:300px;text-align:center}
.feature.left{left:140px}
.feature.mid{left:440px;top:-30px;width:320px;height:400px;border:1px solid var(--line);padding-top:70px}
.feature.right{left:760px}
.feature-icon{width:60px;height:60px;border:2px solid var(--white);border-radius:50%;margin:0 auto;display:flex;align-items:center;justify-content:center}
.feature h3{font-size:19px;font-weight:500;margin-top:22px}
.feature p{font-size:12px;line-height:18px;color:var(--muted);width:250px;margin:14px auto 0}
.btn-small{display:inline-block;margin-top:20px;font-size:11px;border:1px solid var(--white);border-radius:12px;padding:4px 14px}

/* welcome */
.welcome{position:absolute;top:1160px;left:0;width:1200px;height:380px}
.welcome-photo{position:absolute;inset:0;background:linear-gradient(90deg,#1d1a16 0%,#3a3128 30%,#2a2620 60%,#171512 100%)}
.welcome-inner{position:absolute;top:90px;left:0;width:1200px;text-align:center}
.welcome h2{font-size:34px;font-weight:500;letter-spacing:.5px}
.welcome p{width:820px;margin:20px auto 0;font-size:13px;line-height:20px;color:#ddd}
.btn-outline{display:inline-block;margin-top:30px;font-size:13px;font-weight:500;border:1px solid var(--white);padding:9px 18px}

/* listings */
.listings{position:absolute;top:1540px;left:0;width:1200px;height:880px;background:var(--light)}
.listings h2{text-align:center;color:#222;font-size:32px;font-weight:500;margin-top:76px}
.card-grid{position:absolute;top:180px;left:132px;display:grid;grid-template-columns:repeat(3,296px);column-gap:24px;row-gap:22px}
.property-card{background:var(--white);height:318px;position:relative;box-shadow:0 1px 4px rgba(0,0,0,.12)}
.property-photo{height:160px;margin:6px 6px 0}
.tag{position:absolute;top:6px;right:6px;background:#d9d9d9;color:#333;font-size:9px;font-weight:700;padding:6px 10px;letter-spacing:.3px}
.property-card p{color:var(--text);font-size:12px;line-height:18px;padding:14px 14px 0}
.card-foot{position:absolute;left:0;bottom:0;width:100%;height:46px;border-top:1px solid #e2e2e2;display:flex;align-items:center;justify-content:space-between;padding:0 14px;font-size:12px;color:#444}
.card-foot .loc{display:flex;align-items:center;gap:6px}
.photo-a{background:linear-gradient(180deg,#8fb3d6 0%,#b9c9d6 40%,#6b6f6a 70%,#4f6c3e 100%)}
.photo-b{background:linear-gradient(180deg,#a9c6e3 0%,#cdd6da 45%,#9a8d78 70%,#5d8a3c 100%)}
.photo-c{background:linear-gradient(180deg,#7fa4cc 0%,#d8dde0 45%,#8e8a83 70%,#4b7a35 100%)}
.photo-d{background:linear-gradient(180deg,#9dbbe0 0%,#b3a58f 50%,#7e6a55 72%,#5a8a42 100%)}
.photo-e{background:linear-gradient(180deg,#6f9fd4 0%,#d2d4cf 45%,#a39983 70%,#3f7a2f 100%)}
.photo-f{background:linear-gradient(180deg,#94b5d9 0%,#a8998a 50%,#6d5f52 72%,#557a40 100%)}

/* news */
.news{position:absolute;top:2420px;left:0;width:1200px;height:400px;background:var(--black)}
.news h2{position:absolute;top:76px;left:132px;font-size:22px;font-weight:500}
.news-item{position:absolute;top:152px;width:460px;display:flex;gap:20px}
.news-item.first{left:132px}
.news-item.second{left:620px}
.news-photo{width:176px;height:148px;flex:none}
.news-photo.one{background:linear-gradient(160deg,#9db4c6 0%,#6e7a6c 50%,#3d4a36 100%)}
.news-photo.two{background:linear-gradient(160deg,#8fb0d2 0%,#b08d6e 50%,#4a6a34 100%)}
.news-body h3{font-size:15px;font-weight:400}
.news-date{font-size:11px;color:var(--muted);margin-top:8px}
.news-body p{font-size:11px;line-height:16px;color:#cfcfcf;margin-top:8px}
.read-more{font-size:12px;margin-top:10px;display:block}

/* footer */
.site-footer{position:absolute;top:2820px;left:0;width:1200px;height:340px;background:var(--footer)}
.footer-brand{position:absolute;top:110px;left:132px}
.footer-brand .brand-name{font-size:22px}
.social{display:flex;gap:8px;margin-top:16px}
.social span{width:20px;height:20px;border-radius:50%;background:var(--white)}
.footer-col{position:absolute;top:60px}
.footer-col h4{font-size:15px;font-weight:500;margin-bottom:16px;letter-spacing:.3px}
.col-contact{left:368px}
.col-signup{left:652px;width:240px}
.col-links{left:952px}
.contact-row{display:flex;gap:10px;align-items:flex-start;font-size:11px;line-height:16px;color:#cfcfcf;margin-bottom:12px}
.contact-row svg{flex:none;margin-top:2px}
.col-signup p{font-size:11px;line-height:16px;color:#cfcfcf}
.email-field{width:120px;height:26px;background:var(--white);margin-top:12px;color:#888;font-size:10px;padding:7px 8px}
.btn-subscribe{display:inline-block;margin-top:10px;background:#3f3f3f;font-size:10px;font-weight:500;padding:7px 12px}
.col-links ul{list-style:none;font-size:11px;line-height:24px;color:#cfcfcf}
.copyright{position:absolute;top:3160px;left:0;width:1200px;height:48px;background:var(--bar);text-align:center;font-size:11px;color:var(--grey);line-height:48px}
</style>
</head>
<body>

<section class="hero">
  <div class="hero-photo" role="img" aria-label="Dusk view of a luxury lakeside home across calm water framed by green trees"></div>
  <a class="slide-arrow prev" href="#"><svg width="10" height="12" viewBox="0 0 10 12"><path d="M7 1 2 6l5 5" stroke="#fff" stroke-width="2" fill="none"/></svg></a>
  <a class="slide-arrow next" href="#"><svg width="10" height="12" viewBox="0 0 10 12"><path d="M3 1l5 5-5 5" stroke="#fff" stroke-width="2" fill="none"/></svg></a>
  <div class="hero-content">
    <div class="hero-brand"><span class="brand-mark"></span><span class="brand-name">NORTHFIELD</span></div>
    <p class="hero-tagline">Lorem ipsum dolor sit amet conse ctetur adipiscing elit, sed do eiusmod</p>
    <div class="search-bar"><span>Search listing by city &amp; state, zip</span>
      <span class="search-btn"><svg width="18" height="18" viewBox="0 0 18 18"><circle cx="7.5" cy="7.5" r="5.5" stroke="#fff" stroke-width="2" fill="none"/><path d="M11.5 11.5 16 16" stroke="#fff" stroke-width="2"/></svg></span>
    </div>
  </div>
  <svg class="hero-curve" viewBox="0 0 1200 90" preserveAspectRatio="none"><path d="M0 10 Q600 150 1200 10 L1200 90 L0 90Z" fill="#000"/><path d="M0 10 Q600 150 1200 10" stroke="#fff" stroke-width="3" fill="none"/></svg>
</section>

<header class="site-header">
  <a class="brand" href="#"><span class="brand-mark"></span><span class="brand-name">NORTHFIELD</span></a>
  <nav class="main-nav"><a href="#">HOME</a><a href="#">ABOUT QE NO HOME</a><a href="#">RESOURCES</a><a href="#">MY MARKET ANALYSIS</a><a href="#">CONTACT US</a></nav>
</header>

<section class="features">
  <div class="feature left">
    <div class="feature-icon"><svg width="28" height="24" viewBox="0 0 28 24"><path d="M2 22 10 8l5 8 4-5 7 11Z" stroke="#fff" stroke-width="2" fill="none"/></svg></div>
    <h3>Quis autem vel eum</h3>
    <p>Nemo enim ipsam voluptatem quia voluptas sit aspernatur aut odit aut fugit, sed quia consequuntur magni dolores</p>
    <a class="btn-small" href="#">Read More</a>
  </div>
  <div class="feature mid">
    <div class="feature-icon"><svg width="26" height="26" viewBox="0 0 26 26"><path d="M3 3h10l10 10-10 10L3 13Z" stroke="#fff" stroke-width="2" fill="none"/><circle cx="8" cy="8" r="2" fill="#fff"/></svg></div>
    <h3>Quis autem vel eum</h3>
    <p>Nemo enim ipsam voluptatem quia voluptas sit aspernatur aut odit aut fugit, sed quia consequuntur magni dolores</p>
    <a class="btn-small" href="#">Read More</a>
  </div>
  <div class="feature right">
    <div class="feature-icon"><svg width="26" height="26" viewBox="0 0 26 26"><circle cx="13" cy="13" r="10" stroke="#fff" stroke-width="2" fill="none"/><path d="M13 7v12M10 10h5a2 2 0 0 1 0 4h-4a2 2 0 0 0 0 4h5" stroke="#fff" stroke-width="1.6" fill="none"/></svg></div>
    <h3>Quis autem vel eum</h3>
    <p>Nemo enim ipsam voluptatem quia voluptas sit aspernatur aut odit aut fugit, sed quia consequuntur magni dolores</p>
    <a class="btn-small" href="#">Read More</a>
  </div>
</section>

<section class="welcome">
  <div class="welcome-photo" role="img" aria-label="Softly lit wooded lot at dusk behind a dark overlay"></div>
  <div class="welcome-inner">
    <h2>WELCOME TO NORTHFIELD REALTY GROUP</h2>
    <p>Nemo enim ipsam voluptatem quia voluptas sit aspernatur aut odit aut fugit, sed quia consequuntur magni dolores eos qui ratione voluptatem sequi nesciunt. Neque porro quisquam est, qui dolorem ipsum quia dolor sit amet, consectetur, adipisci velit, sed quia non numquam eius modi tempora incidunt.</p>
    <a class="btn-outline" href="#">READ MORE</a>
  </div>
</section>

<section class="listings">
  <h2>PROPERTIES LISTINGS</h2>
  <div class="card-grid">
    <article class="property-card"><div class="property-photo photo-a" role="img" aria-label="Modern two-storey home with lawn"></div><span class="tag">FIND MORE PROPERTIES</span><p>Nemo enim ipsam voluptatem quia voluptas sit aspernatur aut odit aut fugit, sed quia magni dolores.</p><div class="card-foot"><span class="loc"><svg width="10" height="13" viewBox="0 0 10 13"><path d="M5 12S1 7 1 5a4 4 0 0 1 8 0c0 2-4 7-4 7Z" fill="#555"/></svg>Los Angeles, California</span><span>$370,000</span></div></article>
    <article class="property-card"><div class="property-photo photo-b" role="img" aria-label="Large suburban family house with garden"></div><span class="tag">FIND MORE PROPERTIES</span><p>Nemo enim ipsam voluptatem quia voluptas sit aspernatur aut odit aut fugit, sed quia magni dolores.</p><div class="card-foot"><span class="loc"><svg width="10" height="13" viewBox="0 0 10 13"><path d="M5 12S1 7 1 5a4 4 0 0 1 8 0c0 2-4 7-4 7Z" fill="#555"/></svg>Los Angeles, California</span><span>$370,000</span></div></article>
    <article class="property-card"><div class="property-photo photo-c" role="img" aria-label="White colonial-style home on a green lot"></div><span class="tag">FIND MORE PROPERTIES</span><p>Nemo enim ipsam voluptatem quia voluptas sit aspernatur aut odit aut fugit, sed quia magni dolores.</p><div class="card-foot"><span class="loc"><svg width="10" height="13" viewBox="0 0 10 13"><path d="M5 12S1 7 1 5a4 4 0 0 1 8 0c0 2-4 7-4 7Z" fill="#555"/></svg>Los Angeles, California</span><span>$370,000</span></div></article>
    <article class="property-card"><div class="property-photo photo-d" role="img" aria-label="Brick family house with front lawn"></div><span class="tag">FIND MORE PROPERTIES</span><p>Nemo enim ipsam voluptatem quia voluptas sit aspernatur aut odit aut fugit, sed quia magni dolores.</p><div class="card-foot"><span class="loc"><svg width="10" height="13" viewBox="0 0 10 13"><path d="M5 12S1 7 1 5a4 4 0 0 1 8 0c0 2-4 7-4 7Z" fill="#555"/></svg>Los Angeles, California</span><span>$370,000</span></div></article>
    <article class="property-card"><div class="property-photo photo-e" role="img" aria-label="Contemporary home framed by trees and blue sky"></div><span class="tag">FIND MORE PROPERTIES</span><p>Nemo enim ipsam voluptatem quia voluptas sit aspernatur aut odit aut fugit, sed quia magni dolores.</p><div class="card-foot"><span class="loc"><svg width="10" height="13" viewBox="0 0 10 13"><path d="M5 12S1 7 1 5a4 4 0 0 1 8 0c0 2-4 7-4 7Z" fill="#555"/></svg>Los Angeles, California</span><span>$370,000</span></div></article>
    <article class="property-card"><div class="property-photo photo-f" role="img" aria-label="Stone and timber estate home with landscaped yard"></div><span class="tag">FIND MORE PROPERTIES</span><p>Nemo enim ipsam voluptatem quia voluptas sit aspernatur aut odit aut fugit, sed quia magni dolores.</p><div class="card-foot"><span class="loc"><svg width="10" height="13" viewBox="0 0 10 13"><path d="M5 12S1 7 1 5a4 4 0 0 1 8 0c0 2-4 7-4 7Z" fill="#555"/></svg>Los Angeles, California</span><span>$370,000</span></div></article>
  </div>
</section>

<section class="news">
  <h2>LATEST NEWS</h2>
  <article class="news-item first">
    <div class="news-photo one" role="img" aria-label="Agents meeting clients outside a home"></div>
    <div class="news-body"><h3>Nulla at diam ornare, aliquam urna</h3><div class="news-date">MAY 22, 2018</div><p>Nulla at diam ornare, aliquam urna sed, commodo erat. Etiam sit amet mollis lacus, vitae aliquet risus. Donec tristique nibh vel sem lobortis elementum.</p><a class="read-more" href="#">Read More »</a></div>
  </article>
  <article class="news-item second">
    <div class="news-photo two" role="img" aria-label="Family standing in front of their new house"></div>
    <div class="news-body"><h3>Nulla at diam ornare, aliquam urna</h3><div class="news-date">MAY 22, 2018</div><p>Nulla at diam ornare, aliquam urna sed, commodo erat. Etiam sit amet mollis lacus, vitae aliquet risus. Donec tristique nibh vel sem lobortis elementum.</p><a class="read-more" href="#">Read More »</a></div>
  </article>
</section>

<footer class="site-footer">
  <div class="footer-brand">
    <a class="brand" href="#"><span class="brand-mark"></span><span class="brand-name">NORTHFIELD</span></a>
    <div class="social"><span></span><span></span><span></span><span></span></div>
  </div>
  <div class="footer-col col-contact">
    <h4>CONTACT US</h4>
    <div class="contact-row"><svg width="10" height="13" viewBox="0 0 10 13"><path d="M5 12S1 7 1 5a4 4 0 0 1 8 0c0 2-4 7-4 7Z" fill="#ccc"/></svg><span>Northfield Realty Group,<br>218 Lakeview Avenue, Suite 110</span></div>
    <div class="contact-row"><svg width="12" height="12" viewBox="0 0 12 12"><path d="M2 1h3l1 3-2 1a7 7 0 0 0 3 3l1-2 3 1v3c-6 1-10-3-9-9Z" fill="#ccc"/></svg><span>Phone : +1 (555) 014 2288</span></div>
    <div class="contact-row"><svg width="12" height="10" viewBox="0 0 12 10"><rect x="1" y="1" width="10" height="8" stroke="#ccc" fill="none"/><path d="M1 1l5 4 5-4" stroke="#ccc" fill="none"/></svg><span>hello@northfieldrealty.com</span></div>
  </div>
  <div class="footer-col col-signup">
    <h4>SIGN UP TO RECEIVE EMAIL</h4>
    <p>Receive our newest listings and market updates straight to your inbox.</p>
    <div class="email-field">Email Address</div>
    <a class="btn-subscribe" href="#">SUBSCRIBE</a>
  </div>
  <div class="footer-col col-links">
    <h4>QUICK LINKS</h4>
    <ul><li>Home</li><li>Qeno Info</li><li>About Qe No Home</li><li>Download</li><li>Contact Us</li></ul>
  </div>
</footer>
<div class="copyright">Copyright © Northfield Realty Group 2018. All Rights Reserved</div>

</body>
</html>
```